indépendant en tant que Massothérapeute et Préparateur Mental, j'ai besoin de ...

Massothérapeute et préparateur mental indépendant, je recherche une carte de visite sobre et dynamique, sans images liées au massage ou à la préparation mentale mais intégrant mon logo. Les couleurs que j'aime bien sont : Blanc, gris, anthracite, noir et jaune

Contact Information for Business Card

carte de préférence Horizontale
neutre qui puisse toucher le deux domaines Massothérapie et préparation mentale

Requirements
Must have
• mon projet doit intégrer au recto:
LOGO
Loïc Bardèze
078 513 26 48
info@loicbardeze.ch
et éventuellement www.loicbardeze.ch

et au verso les deux adresses:

Chemin des Ormilles 7B
1400 Yverdon-les-Bains

Route de la Gravière 9
1700 Fribourg

Should not have
• mon projet ne doit pas contenir d'image en liens avec le massage ni la préparation mentale.

```html
<!DOCTYPE html>
<html lang="fr">
<head>
<meta charset="utf-8">
<title>Loïc Bardèze – Carte de visite</title>
<link href="https://fonts.googleapis.com/css2?family=Work+Sans:wght@400;500;600&display=swap" rel="stylesheet">
<style>
  :root {
    --bg: #3a3a3a;
    --anthracite: #1c1c1c;
    --anthracite-soft: #262626;
    --emboss: #3b3b3b;
    --emboss-light: #4a4a4a;
    --white: #ffffff;
    --ink: #1a1a1a;
    --grey: #555555;
    --yellow: #f5b41a;
  }
  * { box-sizing: border-box; margin: 0; padding: 0; }
  html, body { width: 1200px; height: 930px; overflow: hidden; }
  body {
    background: var(--bg);
    font-family: "Work Sans", Arial, sans-serif;
    position: relative;
  }
  .card {
    position: absolute;
    left: 290px;
    width: 620px;
    height: 400px;
    border-radius: 22px;
    overflow: hidden;
    box-shadow: 0 10px 30px rgba(0,0,0,.35);
  }
  .card--back { top: 40px; background: var(--anthracite); }
  .card--front { top: 490px; background: var(--white); }

  .brand { position: absolute; display: flex; flex-direction: column; }
  .brand__row { display: flex; align-items: center; gap: 10px; }
  .brand__dot { width: 14px; height: 14px; }
  .brand__name { font-weight: 600; letter-spacing: .02em; }
  .brand__tagline { font-size: 9.5px; letter-spacing: .08em; text-transform: uppercase; margin-top: 4px; margin-left: 24px; }

  .card--back .brand { left: 150px; top: 170px; }
  .card--back .brand__dot { background: var(--emboss); }
  .card--back .brand__name { font-size: 34px; color: var(--emboss-light); }
  .card--back .brand__tagline { color: var(--emboss); font-size: 11px; }

  .card--front .brand { left: 40px; top: 178px; }
  .card--front .brand__dot { background: var(--ink); }
  .card--front .brand__name { font-size: 24px; color: var(--ink); }
  .card--front .brand__tagline { color: var(--grey); font-size: 8px; margin-left: 24px; }

  .divider {
    position: absolute; left: 336px; top: 80px;
    width: 2px; height: 250px; background: var(--yellow);
  }
  .details { position: absolute; left: 362px; top: 72px; color: var(--ink); }
  .details__name { color: var(--yellow); font-size: 25px; font-weight: 500; letter-spacing: .03em; line-height: 1; }
  .details__role { font-size: 15px; margin-top: 6px; }
  .contact { list-style: none; margin-top: 10px; font-size: 15px; line-height: 1.45; }
  .contact li { display: flex; align-items: center; gap: 8px; }
  .contact svg { width: 11px; height: 11px; flex: none; }
  .address { font-size: 15px; line-height: 1.4; margin-top: 10px; }
</style>
</head>
<body>
  <section class="card card--back" aria-label="Verso">
    <div class="brand">
      <div class="brand__row">
        <span class="brand__dot"></span>
        <span class="brand__name">Loïc Bardèze</span>
      </div>
      <span class="brand__tagline">Massothérapeute / Préparateur Mental</span>
    </div>
  </section>

  <section class="card card--front" aria-label="Recto">
    <div class="brand">
      <div class="brand__row">
        <span class="brand__dot"></span>
        <span class="brand__name">Loïc Bardèze</span>
      </div>
      <span class="brand__tagline">Massothérapeute / Préparateur Mental</span>
    </div>

    <div class="divider"></div>

    <div class="details">
      <p class="details__name">LOÏC BARDÈZE</p>
      <p class="details__role">Director</p>
      <ul class="contact">
        <li>
          <svg viewBox="0 0 12 12" aria-hidden="true"><path d="M3 1 L5 3.5 L4 5 Q5 7 7 8 L8.5 7 L11 9 L9.5 11 Q5 11 1 3 Z" fill="var(--yellow)"/></svg>
          078 513 26 48
        </li>
        <li>
          <svg viewBox="0 0 12 12" aria-hidden="true"><rect x="1" y="2.5" width="10" height="7" fill="none" stroke="var(--yellow)" stroke-width="1.3"/><path d="M1 3 L6 7 L11 3" fill="none" stroke="var(--yellow)" stroke-width="1.3"/></svg>
          info@loicbardeze.ch
        </li>
        <li>
          <svg viewBox="0 0 12 12" aria-hidden="true"><circle cx="6" cy="6" r="5" fill="none" stroke="var(--yellow)" stroke-width="1.2"/><ellipse cx="6" cy="6" rx="2" ry="5" fill="none" stroke="var(--yellow)" stroke-width="1"/><path d="M1 6 H11" stroke="var(--yellow)" stroke-width="1"/></svg>
          www.loicbardeze.ch
        </li>
      </ul>
      <p class="address">Chemin des Ormilles 7B<br>1400 Yverdon-les-Bains</p>
      <p class="address">Route de la Gravière 9<br>1700 Fribourg</p>
    </div>
  </section>
</body>
</html>
```